Brightlane Rapid Rinse Web Design

We are looking for a web design that highlights our state of the art fully automated commercial vehicle washing equipment. Similar system to a car wash however this system is meant for the largest vehicles on our roadways. Transport trucks with or without a trailer, busses both highway and school, RV's from 5th wheel type to A Class. Cement trucks, dump trucks, vac trucks, fuel trucks etc. Pick ups with utility trailers...Refrigerator truck clean outs.
Brightlane Rapid Rinse will wash your vehicle quickly and with a minimal impact on the environment

Home page
About us
Why Brightlane
Services and pricing
Videos of wash system
Fleets
contact us

Target Market(s)

Commercial vehicle owners and operators as well as corporate fleets. Includes busses, municipal, school and highway.both school and

Industry/Entity Type

transportation

Coding

Coded - Design and coding required

Number of Pages Required

5+ page

Font styles to use
Sans Serif

Colors
0054AA
0677BA
7BADD7
CADEEF
E8F1F8

Requirements
Must have
• Welcome page,why us page which describes the financial and environmental benefits. payment processing page, contact us page, Services which is washing vehicles and greasing for commercial vehicles that want that service and grease
Nice to have
• pictures of both clean and dirty commercial vehicles ie. before and after

```html
<!DOCTYPE html>
<html lang="en">
<head>
<meta charset="utf-8">
<title>Brightlane Rapid Rinse</title>
<link href="https://fonts.googleapis.com/css2?family=Exo+2:wght@400;500;600&family=Mulish:wght@400;600;700&display=swap" rel="stylesheet">
<style>
:root{
  --blue:#0054AA;
  --mid:#0677BA;
  --sky:#7BADD7;
  --pale:#CADEEF;
  --mist:#E8F1F8;
  --ink:#1d2733;
  --muted:#4a5563;
  --white:#ffffff;
  --photo-grey:#98a4ae;
  --photo-steel:#8796a3;
  --photo-warm:#7a6d58;
  --photo-red:#8f4a52;
}
*{box-sizing:border-box;margin:0;padding:0}
html,body{width:1200px;height:5268px;overflow:hidden}
body{position:relative;font-family:"Mulish",sans-serif;color:var(--ink);background:var(--white)}
.abs{position:absolute}
h2.section-title{position:absolute;left:0;width:1200px;text-align:center;font-family:"Exo 2",sans-serif;font-weight:500;font-size:31px;letter-spacing:1px;color:var(--ink)}
.title-rule{position:absolute;left:586px;width:28px;height:3px;background:var(--blue)}
.btn{position:absolute;display:flex;align-items:center;justify-content:center;font-size:13px;font-weight:600;letter-spacing:.3px;text-transform:uppercase}
.btn-solid{background:var(--blue);color:var(--white)}
.btn-light{background:var(--white);color:var(--blue)}

/* header */
.site-header{position:absolute;top:0;left:0;width:1200px;height:98px;background:var(--white)}
.brand{position:absolute;left:129px;top:32px;font-family:"Exo 2",sans-serif;font-size:27px;font-weight:500;color:var(--blue)}
.contact-tab{position:absolute;left:606px;top:0;width:462px;height:52px;background:var(--blue);border-radius:0 0 0 22px;display:flex;align-items:center;justify-content:center;gap:20px;color:var(--white);font-size:13px;clip-path:polygon(4% 0,100% 0,100% 100%,0 100%)}
.contact-tab span{display:flex;align-items:center;gap:6px}
.main-nav{position:absolute;top:98px;left:0;width:1200px;height:41px;background:var(--blue)}
.main-nav ul{list-style:none;position:absolute;left:131px;top:0;display:flex;height:41px}
.main-nav li{height:41px;display:flex;align-items:center;padding:0 38px;color:var(--white);font-size:14px;letter-spacing:.4px}
.main-nav li.active{padding:0 30px;background:var(--white);color:var(--blue);font-weight:700}

/* hero */
.hero{position:absolute;top:139px;left:0;width:1200px;height:638px;overflow:hidden}
.hero-photo{position:absolute;inset:0 0 120px 0;background:linear-gradient(180deg,#8e9aa4,#a9b5bf)}
.hero h1{position:absolute;left:127px;top:104px;font-family:"Exo 2",sans-serif;font-weight:500;font-size:46px;line-height:52px;letter-spacing:2px;color:var(--white);text-transform:uppercase}
.hero .btn{top:301px;height:41px}
.dots{position:absolute;top:518px;left:560px;display:flex;gap:8px}
.dots i{display:block;width:12px;height:12px;border-radius:50%;background:var(--white)}
.dots i.on{background:var(--mid)}

/* services */
.price-card{position:absolute;top:938px;width:300px;height:507px;background:linear-gradient(#ffffff 40%,var(--mist));box-shadow:0 2px 10px rgba(0,40,90,.08)}
.price-card .photo{position:absolute;left:0;top:0;width:300px;height:207px}
.price-badge{position:absolute;right:12px;top:166px;width:92px;height:92px;border-radius:50%;background:var(--mid);border:4px solid var(--white);color:var(--white);text-align:center;padding-top:16px}
.price-badge b{display:block;font-family:"Exo 2",sans-serif;font-size:28px;font-weight:500;line-height:32px}
.price-badge small{font-size:11px}
.price-card h3{position:absolute;left:35px;top:234px;font-family:"Exo 2",sans-serif;font-weight:500;font-size:23px;line-height:29px;color:var(--mid)}
.price-card p{position:absolute;left:35px;top:315px;width:230px;font-size:11.5px;line-height:17px;color:var(--muted)}
.price-card .btn{left:35px;top:407px;width:110px;height:35px;font-size:11px}

/* why */
.why{position:absolute;top:1482px;left:0;width:1200px;height:736px;background:linear-gradient(160deg,#0a4aa0 0%,var(--blue) 50%,var(--mid) 100%);overflow:hidden}
.why h2{position:absolute;top:70px;left:0;width:1200px;text-align:center;color:var(--white);font-family:"Exo 2",sans-serif;font-weight:500;font-size:31px;letter-spacing:1px}
.why .rule{position:absolute;top:136px;left:586px;width:28px;height:3px;background:var(--white)}
.why .lead{position:absolute;top:170px;left:250px;width:700px;text-align:center;color:var(--white);font-size:18px;line-height:29px}
.why .btn{top:262px;left:526px;width:148px;height:41px}
.benefit{position:absolute;width:220px;text-align:center}
.benefit .ring{width:92px;height:92px;margin:0 auto;border-radius:50%;background:var(--white);box-shadow:0 2px 8px rgba(0,40,90,.25);display:flex;align-items:center;justify-content:center}
.benefit .ring span{width:78px;height:78px;border-radius:50%;background:var(--mid);display:flex;align-items:center;justify-content:center}
.benefit h4{font-family:"Exo 2",sans-serif;font-weight:500;font-size:18px;color:var(--mid);margin-top:24px;letter-spacing:.5px}
.benefit p{font-size:12px;line-height:18px;color:var(--muted);margin-top:10px}

/* fleets */
.fleets{position:absolute;top:2218px;left:0;width:1200px;height:587px;background:var(--mist)}
.fleet{position:absolute;top:176px;width:227px;text-align:center}
.fleet .photo{width:227px;height:231px;background:var(--photo-steel)}
.fleet span{display:block;margin-top:25px;font-size:16px;color:var(--mid);letter-spacing:.4px}

/* mission */
.mission{position:absolute;top:2805px;left:0;width:1200px;height:288px;background:var(--blue);color:var(--white);text-align:center}
.mission h2{position:absolute;top:50px;width:1200px;font-family:"Exo 2",sans-serif;font-weight:500;font-size:31px;letter-spacing:1px}
.mission .rule{position:absolute;top:114px;left:586px;width:28px;height:3px;background:var(--white)}
.mission p{position:absolute;top:160px;left:180px;width:840px;font-size:14.5px;line-height:24px}

/* before after */
.compare{position:absolute;top:3262px;left:131px;width:936px;height:313px}
.compare .half{position:absolute;top:0;height:313px}
.compare .divider{position:absolute;left:467px;top:0;width:3px;height:357px;background:var(--blue)}
.compare-label{position:absolute;top:3594px;font-size:18px;letter-spacing:1px;color:var(--ink)}
.chev{position:absolute}

/* video */
.video{position:absolute;top:3690px;left:0;width:1200px;height:474px;background:linear-gradient(180deg,#8c6b72,#7d858d)}
.video .play{position:absolute;left:563px;top:174px;width:72px;height:72px;border-radius:50%;background:#e5322d;display:flex;align-items:center;justify-content:center}
.video h3{position:absolute;top:286px;width:1200px;text-align:center;font-family:"Exo 2",sans-serif;font-weight:500;font-size:33px;color:var(--white);letter-spacing:1.5px;text-shadow:0 2px 6px rgba(0,0,0,.35)}

/* testimonials */
.testimonials{position:absolute;top:4164px;left:0;width:1200px;height:760px;background:linear-gradient(var(--mist),#dbe9f4)}
.quote-card{position:absolute;top:184px;width:288px;height:359px;background:var(--white);padding:26px 35px}
.quote-card .mark{font-family:"Exo 2",sans-serif;font-size:54px;line-height:40px;color:var(--blue);font-weight:600;height:36px}
.quote-card .stars{display:flex;gap:2px;margin-top:10px}
.quote-card p{margin-top:14px;font-size:12.5px;line-height:18.5px;color:var(--muted)}
.quote-card .who{position:absolute;left:35px;top:300px;font-size:12px;font-weight:700;color:var(--blue)}
.quote-card .who::before{content:"";display:block;width:28px;height:2px;background:var(--blue);margin-bottom:20px}

/* footer */
.site-footer{position:absolute;top:4905px;left:0;width:1200px;height:363px;background:var(--blue);color:var(--white)}
.foot-brand{position:absolute;left:129px;top:98px;font-family:"Exo 2",sans-serif;font-size:33px;line-height:45px;font-weight:400}
.foot-col h5{font-size:13px;font-weight:700;letter-spacing:.4px;padding-bottom:8px;border-bottom:2px solid var(--white)}
.foot-col{position:absolute;top:30px}
.foot-row{display:flex;gap:14px;align-items:center;margin-top:20px;font-size:11.5px;line-height:15px}
.foot-row i{width:22px;height:22px;border-radius:50%;background:var(--white);display:flex;align-items:center;justify-content:center;flex:none}
.foot-menu{list-style:none;margin-top:12px;font-size:11.5px;line-height:19.5px}
.socials{display:flex;gap:10px;margin-top:22px}
.socials span{width:32px;height:32px;border-radius:50%;border:2.5px solid var(--white)}
.foot-base{position:absolute;left:131px;top:260px;width:936px;border-top:1px solid rgba(255,255,255,.35)}
.legal{position:absolute;top:300px;width:1200px;text-align:center;font-size:11.5px}
</style>
</head>
<body>

<header class="site-header">
  <div class="brand">Brightlane Rapid Rinse</div>
  <div class="contact-tab">
    <span><svg width="12" height="9" viewBox="0 0 12 9"><rect x=".5" y=".5" width="11" height="8" fill="none" stroke="#fff"/><path d="M.5 .5 6 5 11.5 .5" fill="none" stroke="#fff"/></svg>info@BrightlaneRapidRinse.com</span>
    <span><svg width="12" height="12" viewBox="0 0 24 24"><path fill="#fff" d="M6.6 10.8a15 15 0 0 0 6.6 6.6l2.2-2.2c.3-.3.7-.4 1-.2 1.1.4 2.3.6 3.6.6.6 0 1 .4 1 1V20c0 .6-.4 1-1 1A17 17 0 0 1 3 4c0-.6.4-1 1-1h3.5c.6 0 1 .4 1 1 0 1.3.2 2.5.6 3.6.1.3 0 .7-.2 1z"/></svg>+1 555 014 2200</span>
  </div>
</header>
<nav class="main-nav">
  <ul>
    <li class="active">HOME</li><li>ABOUT US</li><li>SERVICES</li><li>PRICING</li><li>TESTIMONIALS</li><li>CONTACT US</li>
  </ul>
</nav>

<section class="hero">
  <div class="hero-photo" role="img" aria-label="Transport truck inside an automated wash bay"></div>
  <svg class="abs" style="left:0;top:420px" width="1200" height="218" viewBox="0 0 1200 218" aria-hidden="true">
    <defs>
      <linearGradient id="heroWater" x1="0" y1="0" x2="0" y2="1"><stop offset="0" stop-color="#0677BA"/><stop offset=".5" stop-color="#7BADD7"/><stop offset="1" stop-color="#ffffff"/></linearGradient>
    </defs>
    <path d="M0 40 C200 110 380 90 560 60 S900 -10 1200 70 V218 H0Z" fill="url(#heroWater)"/>
    <path d="M0 95 C260 150 520 120 760 100 S1050 110 1200 140 V218 H0Z" fill="#ffffff" opacity=".75"/>
    <path d="M0 150 C300 175 700 140 1200 175 V218 H0Z" fill="#ffffff"/>
  </svg>
  <h1>Speed less than<br>15 minutes and<br>quality</h1>
  <div class="btn btn-solid" style="left:131px;width:150px">Book a wash</div>
  <div class="btn btn-solid" style="left:289px;width:134px">Learn more</div>
  <div class="btn btn-solid" style="left:431px;width:136px">Contact us</div>
  <div class="dots"><i class="on"></i><i></i><i></i><i></i></div>
</section>

<h2 class="section-title" style="top:818px">SERVICES AND PRICING</h2>
<div class="title-rule" style="top:891px"></div>

<article class="price-card" style="left:131px">
  <div class="photo" role="img" aria-label="Truck entering an automated wash tunnel" style="background:var(--photo-grey)"></div>
  <div class="price-badge"><b>$59</b><small>Per Month</small></div>
  <h3>Automated<br>Truck Wash</h3>
  <p>Lorem ipsum dolor sit amet, conse ctetur adipiscing elit, sed do eiusmod tempor incididunt ut labore et dolore magna aliqua. Ut enim</p>
  <div class="btn btn-solid">Learn more</div>
</article>
<article class="price-card" style="left:450px">
  <div class="photo" role="img" aria-label="Oil being poured into a truck engine" style="background:var(--photo-warm)"></div>
  <div class="price-badge"><b>$69</b><small>Per Month</small></div>
  <h3>Additional<br>Services</h3>
  <p>Lorem ipsum dolor sit amet, conse ctetur adipiscing elit, sed do eiusmod tempor incididunt ut labore et dolore magna aliqua. Ut enim</p>
  <div class="btn btn-solid">Learn more</div>
</article>
<article class="price-card" style="left:767px">
  <div class="photo" role="img" aria-label="Wash bay with rotating brushes" style="background:var(--photo-grey)"></div>
  <div class="price-badge"><b>$79</b><small>Per Month</small></div>
  <h3>Fleet<br>Services</h3>
  <p>Lorem ipsum dolor sit amet, conse ctetur adipiscing elit, sed do eiusmod tempor incididunt ut labore et dolore magna aliqua. Ut enim</p>
  <div class="btn btn-solid">Learn more</div>
</article>

<section class="why">
  <h2>WHY BRIGHTLANE</h2>
  <div class="rule"></div>
  <p class="lead">Lorem ipsum dolor sit amet, conse ctetur adipiscing elit, sed do eiusmod tempor incididunt ut labore et dolore magna aliqua.</p>
  <div class="btn btn-light">Book a wash</div>
  <svg class="abs" style="left:0;top:0" width="1200" height="736" viewBox="0 0 1200 736" aria-hidden="true">
    <path d="M0 515 C150 470 300 455 480 470 C640 482 700 420 860 405 C1000 392 1100 390 1200 380 V736 H0Z" fill="#ffffff"/>
    <path d="M0 700 C250 660 500 690 750 660 C950 636 1100 640 1200 650 V736 H0Z" fill="#E8F1F8"/>
  </svg>
  <div class="benefit" style="left:121px;top:444px">
    <div class="ring"><span><svg width="40" height="40" viewBox="0 0 40 40" fill="none" stroke="#fff" stroke-width="2"><rect x="6" y="10" width="28" height="20" rx="2"/><path d="M10 24h20M13 18h14"/><circle cx="13" cy="30" r="2"/><circle cx="27" cy="30" r="2"/><path d="M12 6v3M20 5v4M28 6v3"/></svg></span></div>
    <h4>SPEED WASH</h4>
    <p>Lorem ipsum dolor sit amet, conse ctetur adipiscing elit, sed do eius mod tempor incididunt ut labo re et dolore magna .</p>
  </div>
  <div class="benefit" style="left:366px;top:424px">
    <div class="ring"><span><svg width="40" height="40" viewBox="0 0 40 40" fill="none" stroke="#fff" stroke-width="2.2"><path d="M9 24v-5a11 11 0 0 1 22 0v5"/><rect x="7" y="21" width="6" height="9" rx="2"/><rect x="27" y="21" width="6" height="9" rx="2"/><path d="M30 30c0 3-4 5-8 5"/></svg></span></div>
    <h4>SUPPORT</h4>
    <p>Lorem ipsum dolor sit amet, conse ctetur adipiscing elit, sed do eius mod tempor incididunt ut labo re et dolore magna .</p>
  </div>
  <div class="benefit" style="left:616px;top:373px">
    <div class="ring"><span><svg width="40" height="40" viewBox="0 0 40 40" fill="none" stroke="#fff" stroke-width="2"><path d="M20 5l2 4 4 .5-3 3 .8 4-3.8-2-3.8 2 .8-4-3-3 4-.5z"/><rect x="8" y="22" width="10" height="12"/><path d="M22 26h10M22 31h8"/></svg></span></div>
    <h4>SATISFACTION</h4>
    <p>Lorem ipsum dolor sit amet, conse ctetur adipiscing elit, sed do eius mod tempor incididunt ut labo re et dolore magna .</p>
  </div>
  <div class="benefit" style="left:861px;top:373px">
    <div class="ring"><span><svg width="40" height="40" viewBox="0 0 40 40" fill="none" stroke="#fff" stroke-width="2.2"><circle cx="20" cy="20" r="14"/><path d="M14 20l4 4 8-8"/></svg></span></div>
    <h4 style="margin-top:16px">QUALITY</h4>
    <p>Lorem ipsum dolor sit amet, conse ctetur adipiscing elit, sed do eius mod tempor incididunt ut labo re et dolore magna .</p>
  </div>
</section>

<section class="fleets">
  <h2 class="section-title" style="top:60px">FLEETS</h2>
  <div class="title-rule" style="top:126px"></div>
  <div class="fleet" style="left:131px"><div class="photo" role="img" aria-label="Cement mixer truck"></div><span>CEMENT TRUCKS</span></div>
  <div class="fleet" style="left:370px"><div class="photo" role="img" aria-label="Dump truck unloading gravel"></div><span>DUMP TRUCKS</span></div>
  <div class="fleet" style="left:605px"><div class="photo" role="img" aria-label="Vacuum truck"></div><span>VAC TRUCKS</span></div>
  <div class="fleet" style="left:842px"><div class="photo" role="img" aria-label="Fuel tanker truck"></div><span>FUEL TRUCKS</span></div>
  <div class="btn btn-solid" style="left:530px;top:496px;width:140px;height:36px;font-size:11px">View all fleets</div>
</section>

<section class="mission">
  <h2>MISSION</h2>
  <div class="rule"></div>
  <p>Sed ut perspiciatis unde omnis iste natus error sit voluptatem accusantium doloremque laudantium, totam rem aperiam, eaque ipsa quae ab illo inventore veritatis et quasi architecto beatae vitae dicta sunt explicabo. Nemo enim ipsam voluptatem quia voluptas sit aspernatur aut odit aut fugit, sed quia consequuntur</p>
</section>

<h2 class="section-title" style="top:3142px">BEFORE AND AFTER</h2>
<div class="title-rule" style="top:3209px"></div>
<div class="compare">
  <div class="half" role="img" aria-label="Dusty tanker truck before washing" style="left:0;width:468px;background:#8a877e"></div>
  <div class="half" role="img" aria-label="Clean tanker truck after washing" style="left:468px;width:468px;background:#9aa7b4"></div>
  <div class="divider"></div>
</div>
<div class="compare-label" style="left:330px">BEFORE</div>
<div class="compare-label" style="left:816px">AFTER</div>
<svg class="chev" style="left:60px;top:3390px" width="24" height="48" viewBox="0 0 24 48"><path d="M20 2 4 24l16 22" fill="none" stroke="#7BADD7" stroke-width="2"/></svg>
<svg class="chev" style="left:1116px;top:3390px" width="24" height="48" viewBox="0 0 24 48"><path d="M4 2l16 22L4 46" fill="none" stroke="#7BADD7" stroke-width="2"/></svg>

<section class="video" role="img" aria-label="Video still of the wash system brushes in a truck bay">
  <div class="play"><svg width="26" height="30" viewBox="0 0 26 30"><path d="M2 1l23 14L2 29z" fill="#fff"/></svg></div>
  <h3>EXPRESS WASH SYSTEM</h3>
</section>

<section class="testimonials">
  <h2 class="section-title" style="top:60px">TESTIMONIALS</h2>
  <div class="title-rule" style="top:126px"></div>
  <article class="quote-card" style="left:131px">
    <div class="mark">“</div>
    <div class="stars"><svg width="86" height="15" viewBox="0 0 86 15"><g fill="#0054AA"><path id="st" d="M7.5 0l2.2 4.7 5 .6-3.7 3.5 1 5-4.5-2.5L3 13.8l1-5L.3 5.3l5-.6z"/><use href="#st" x="17.6"/><use href="#st" x="35.2"/><use href="#st" x="52.8"/><use href="#st" x="70.4"/></g></svg></div>
    <p>Sed ut perspiciatis unde omnis iste natus error sit voluptatem accus antium doloremque lauda ntium, totam rem aperiam, eaque ipsa quae ab illo inventore verit atis et quasi architecto beatae vitae dicta sunt explicabo. Nemo enim ipsam voluptatem quia voluptas.</p>
    <div class="who">DANIEL</div>
  </article>
  <article class="quote-card" style="left:456px">
    <div class="mark">“</div>
    <div class="stars"><svg width="86" height="15" viewBox="0 0 86 15"><g fill="#0054AA"><use href="#st"/><use href="#st" x="17.6"/><use href="#st" x="35.2"/><use href="#st" x="52.8"/><use href="#st" x="70.4"/></g></svg></div>
    <p>Sed ut perspiciatis unde omnis iste natus error sit voluptatem accus antium doloremque lauda ntium, totam rem aperiam, eaque ipsa quae ab illo inventore verit atis et quasi architecto beatae vitae dicta sunt explicabo. Nemo enim ipsam voluptatem quia voluptas.</p>
    <div class="who">DANIEL</div>
  </article>
  <article class="quote-card" style="left:779px">
    <div class="mark">“</div>
    <div class="stars"><svg width="86" height="15" viewBox="0 0 86 15"><g fill="#0054AA"><use href="#st"/><use href="#st" x="17.6"/><use href="#st" x="35.2"/><use href="#st" x="52.8"/><use href="#st" x="70.4"/></g></svg></div>
    <p>Sed ut perspiciatis unde omnis iste natus error sit voluptatem accus antium doloremque lauda ntium, totam rem aperiam, eaque ipsa quae ab illo inventore verit atis et quasi architecto beatae vitae dicta sunt explicabo. Nemo enim ipsam voluptatem quia voluptas.</p>
    <div class="who">DANIEL</div>
  </article>
  <svg class="chev" style="left:46px;top:340px" width="24" height="48" viewBox="0 0 24 48"><path d="M20 2 4 24l16 22" fill="none" stroke="#0054AA" stroke-width="3"/></svg>
  <svg class="chev" style="left:1118px;top:340px" width="24" height="48" viewBox="0 0 24 48"><path d="M4 2l16 22L4 46" fill="none" stroke="#0054AA" stroke-width="3"/></svg>
  <svg class="abs" style="left:0;top:560px" width="1200" height="200" viewBox="0 0 1200 200" aria-hidden="true">
    <defs><linearGradient id="footWater" x1="0" y1="0" x2="0" y2="1"><stop offset="0" stop-color="#7BADD7"/><stop offset=".55" stop-color="#0677BA"/><stop offset="1" stop-color="#0054AA"/></linearGradient></defs>
    <path d="M0 60 C200 20 420 110 650 80 S1000 20 1200 50 V200 H0Z" fill="url(#footWater)"/>
    <path d="M0 110 C300 80 600 150 900 120 S1120 100 1200 110 V200 H0Z" fill="#0054AA" opacity=".8"/>
  </svg>
</section>

<footer class="site-footer">
  <div class="foot-brand">Brightlane<br>Rapid Rinse</div>
  <div class="foot-col" style="left:409px;width:193px">
    <h5>CONTACT US</h5>
    <div class="foot-row"><i><svg width="10" height="12" viewBox="0 0 10 12"><path d="M5 0a4 4 0 0 1 4 4c0 3-4 8-4 8S1 7 1 4a4 4 0 0 1 4-4z" fill="#0054AA"/><circle cx="5" cy="4" r="1.5" fill="#fff"/></svg></i><span>Orchard Row 14,<br>4410 Fenwick</span></div>
    <div class="foot-row"><i><svg width="11" height="11" viewBox="0 0 24 24"><path fill="#0054AA" d="M6.6 10.8a15 15 0 0 0 6.6 6.6l2.2-2.2c.3-.3.7-.4 1-.2 1.1.4 2.3.6 3.6.6.6 0 1 .4 1 1V20c0 .6-.4 1-1 1A17 17 0 0 1 3 4c0-.6.4-1 1-1h3.5c.6 0 1 .4 1 1 0 1.3.2 2.5.6 3.6.1.3 0 .7-.2 1z"/></svg></i><span>Call Us<br>+1 555 014 2200</span></div>
    <div class="foot-row"><i><svg width="11" height="8" viewBox="0 0 12 9"><rect x=".5" y=".5" width="11" height="8" fill="#0054AA"/><path d="M.5 .5 6 5 11.5 .5" fill="none" stroke="#fff"/></svg></i><span>E mail Us<br>info@BrightlaneRapidRinse.com</span></div>
  </div>
  <div class="foot-col" style="left:699px;width:106px">
    <h5>MENU</h5>
    <ul class="foot-menu"><li>Home</li><li>About Us</li><li>Services</li><li>Pricing</li><li>Testimonials</li><li>Contact Us</li></ul>
  </div>
  <div class="foot-col" style="left:873px;width:200px">
    <h5 style="border:none">FOLLOW US</h5>
    <div class="socials"><span></span><span></span><span></span><span></span><span></span></div>
  </div>
  <div class="foot-base"></div>
  <div class="legal">Privacy Policy &nbsp;&nbsp; | &nbsp;&nbsp; Copyright © 2024 All Rights Reserved</div>
</footer>

</body>
</html>
```